We want to revamp our current website -www.kelvota-eng.com

We need to have a new website for our company that offers non-destructive and testing solutions around Africa. We have a current website but it does not fulfil our needs as it is:<br/>1. Not clear and bright<br/>2. Does not fit well in mobile <br/>3. Is not easily updatable by our staff. <br/>4. Is not linked to our social media sites.<br/>We would like to have a website that addresses the above issues. Our colours are Red and Blue and should communicate to our clients, that we are a professional company open for business, ready to solve their non-destructive testing problems around Africa. * Helpful if it is a wordpress website.

Target Market(s)

Our customers are B2B Corporate clients. We mainly work in
1. Storage Terminals
2. Refineries
3. Oil and Gas offshore and onshore rigs.

Industry/Entity Type

Oil And Gas

Contact Information for Business Card

Please find our current business card on the uploaded files.

Coding

Coded - Design and coding required

Number of Pages Required

5+ page

Font styles to use
Serif
Sans Serif

Requirements
Must have
• I like this site www.pirelo-inspection.com They are in the same industry.
• I don't understand how to call them but all the 'call to action' buttons, and links to our Social media pages.
• Must have a place where we update information in a regular basis. A Blog!

```html
<!DOCTYPE html>
<html lang="en">
<head>
<meta charset="utf-8">
<title>Kelvota Engineering – Inspection and Engineering Services</title>
<link rel="stylesheet" href="https://fonts.googleapis.com/css2?family=Lato:wght@400;700;900&family=Roboto:wght@400;500;700&display=swap">
<style>
:root{
  --red:#a8091a;
  --red-deep:#8c0514;
  --navy:#1b2358;
  --navy-dark:#141a45;
  --lavender:#e9ebf6;
  --white:#ffffff;
  --ink:#2a2d3a;
  --muted:#555a66;
}
*{margin:0;padding:0;box-sizing:border-box}
html,body{width:1200px;height:3725px;overflow:hidden}
body{position:relative;background:var(--white);font-family:'Roboto',Arial,sans-serif;color:var(--ink)}
.abs{position:absolute}
.heading{font-family:'Lato',Arial,sans-serif;font-weight:400;letter-spacing:.5px}
.heading b{font-weight:900}
.pill{position:absolute;display:flex;align-items:center;justify-content:center;border-radius:30px;font-family:'Roboto',Arial,sans-serif;font-weight:500;text-transform:uppercase;text-decoration:none}
.pill-outline-navy{border:3px solid var(--navy);color:var(--navy);font-size:16px}
.pill-outline-white{border:2px solid var(--white);color:var(--white);font-size:14px}

/* header */
.site-header{position:absolute;left:0;top:0;width:1200px;height:103px;background:var(--white);box-shadow:0 1px 4px rgba(0,0,0,.12);z-index:3}
.brand{position:absolute;left:145px;top:16px;display:flex;align-items:center;gap:14px}
.brand-dot{width:70px;height:70px;border-radius:50%;background:var(--red)}
.brand-name{font-family:'Lato',Arial,sans-serif;font-weight:700;color:var(--red);font-size:24px;line-height:27px}
.main-nav a{position:absolute;top:43px;font-size:15px;font-weight:500;color:var(--navy);text-decoration:none;white-space:nowrap}
.main-nav a.active{color:var(--red)}
.main-nav a.active::after{content:"";position:absolute;left:0;right:0;top:25px;height:3px;background:var(--navy)}

/* hero */
.hero-title{left:0;width:1200px;top:214px;text-align:center;color:var(--white);font-size:53px;line-height:53px;font-family:'Lato',Arial,sans-serif;font-weight:700}
.hero-title span{display:block;font-weight:400}
.hero-btn{left:490px;top:346px;width:208px;height:59px;background:var(--red);color:var(--white);font-size:19px;font-weight:700}

/* about */
.about-title{left:581px;top:840px;font-size:38px;color:var(--ink)}
.about-lead{left:583px;top:908px;width:510px;font-size:17.5px;line-height:27px;color:#3b3e4a}
.about-body{left:583px;top:978px;width:510px;font-size:15.5px;line-height:27px;color:#4b4f5a}
.about-btn{left:580px;top:1084px;width:182px;height:52px}

/* services */
.services-title{left:0;width:1200px;top:1313px;text-align:center;color:var(--white);font-size:41px}
.services-text{left:180px;width:840px;top:1377px;text-align:center;color:var(--white);font-size:17.5px;line-height:27px}
.service-card{position:absolute;top:1494px;width:307px;height:306px}
.service-card h3{position:absolute;left:0;right:0;top:136px;text-align:center;color:var(--white);font-family:'Lato',Arial,sans-serif;font-size:25px;line-height:29px;font-weight:700}
.service-card h3 span{display:block;font-weight:400}
.service-card .pill{left:70px;top:216px;width:157px;height:46px}
.service-card svg.icon{position:absolute;left:118px;top:46px}

/* blogs */
.blogs-title{left:0;width:1200px;top:1906px;text-align:center;color:var(--navy);font-size:37px}
.blog-card{position:absolute;top:1991px;width:466px;height:306px;background:var(--white)}
.blog-card .thumb{position:absolute;left:0;top:0;width:233px;height:306px}
.blog-card .text{position:absolute;left:258px;top:40px;width:190px}
.blog-date{font-size:13px;font-weight:700;color:var(--red);display:flex;align-items:center;gap:5px}
.blog-title{margin-top:8px;font-size:17px;line-height:24px;font-weight:500;color:var(--ink)}
.blog-excerpt{margin-top:10px;font-size:14px;line-height:24px;color:#4d505b}
.blog-more{display:block;margin-top:14px;font-size:14px;font-weight:500;color:var(--red);text-decoration:none}

/* sectors */
.sectors-title{left:139px;top:2570px;color:var(--red);font-size:37px;line-height:34px}
.sectors-text{left:139px;top:2651px;width:230px;font-size:16.5px;line-height:27px;color:#4b4f5a}
.sectors-btn{left:132px;top:2724px;width:161px;height:46px;font-size:15px}
.sector-tile{position:absolute;top:2558px;width:219px;height:210px;border-bottom:6px solid var(--navy)}
.sector-tile span{position:absolute;left:16px;bottom:18px;color:var(--white);font-family:'Lato',Arial,sans-serif;font-size:20px;font-weight:700}

/* contact */
.contact-band{left:0;top:2902px;width:1200px;height:411px;background:linear-gradient(135deg,#a30d1c 0%,#8f0a17 45%,#b3121f 100%)}
.contact-title{left:0;width:1200px;top:2996px;text-align:center;color:var(--white);font-size:40px}
.contact-text{left:200px;width:800px;top:3056px;text-align:center;color:var(--white);font-size:17.5px;line-height:27px}
.contact-btn{left:503px;top:3168px;width:179px;height:49px;background:var(--white);color:var(--navy);font-size:16px;border-radius:30px}

/* footer */
.site-footer{left:0;top:3313px;width:1200px;height:328px;background:var(--navy)}
.footer-brand{position:absolute;left:150px;top:96px;display:flex;align-items:center;gap:12px}
.footer-brand .brand-dot{width:56px;height:56px;background:var(--white)}
.footer-brand .brand-name{color:var(--white);font-size:22px;line-height:25px}
.footer-col{position:absolute;top:70px;color:var(--white)}
.footer-col h4{font-size:17px;font-weight:700;letter-spacing:.3px;margin-bottom:12px}
.footer-col li{list-style:none;font-size:15px;line-height:27.5px;color:#dfe1ee}
.social{display:flex;gap:6px;margin-top:4px}
.social span{width:38px;height:38px;border:2px solid var(--white);border-radius:50%}
.copyright{left:0;top:3641px;width:1200px;height:84px;background:var(--navy-dark);color:#aeb2c8;font-size:13px;text-align:center;line-height:72px}
</style>
</head>
<body>

<header class="site-header">
  <div class="brand">
    <div class="brand-dot"></div>
    <div class="brand-name">KELVOTA<br>ENGINEERING</div>
  </div>
  <nav class="main-nav">
    <a class="active" style="left:458px">HOME</a>
    <a style="left:544px">ABOUT US</a>
    <a style="left:659px">SERVICES <svg width="14" height="10" viewBox="0 0 14 10"><path d="M2 2l5 5 5-5" fill="none" stroke="#1b2358" stroke-width="2"/></svg></a>
    <a style="left:772px">BLOGS</a>
    <a style="left:863px">PROJECTS</a>
    <a style="left:980px">CONTACT</a>
  </nav>
</header>

<!-- hero -->
<svg class="abs" style="left:0;top:103px" width="1200" height="660" viewBox="0 0 1200 660" role="img" aria-label="Night view of an oil storage terminal with lit tanks">
  <defs>
    <linearGradient id="heroGrad" x1="0" y1="0" x2="0" y2="1">
      <stop offset="0" stop-color="#1d2127"/>
      <stop offset=".45" stop-color="#3a3a38"/>
      <stop offset=".7" stop-color="#6b4b25"/>
      <stop offset="1" stop-color="#2a2b2f"/>
    </linearGradient>
  </defs>
  <polygon points="0,0 1200,0 1200,565 600,659 0,565" fill="url(#heroGrad)"/>
  <path d="M88 280l-22 23 22 23" fill="none" stroke="#fff" stroke-width="4"/>
  <path d="M1110 280l22 23-22 23" fill="none" stroke="#fff" stroke-width="4"/>
  <circle cx="565" cy="610" r="6" fill="none" stroke="#fff" stroke-width="2"/>
  <circle cx="588" cy="610" r="6.5" fill="#fff"/>
  <circle cx="610" cy="610" r="6.5" fill="#fff"/>
  <circle cx="632" cy="610" r="6.5" fill="#fff"/>
</svg>
<h1 class="abs hero-title">INSPECTION AND<span>ENGINEERING SERVICES</span></h1>
<a class="pill hero-btn">LEARN MORE</a>

<!-- about -->
<svg class="abs" style="left:140px;top:825px" width="404" height="336" viewBox="0 0 404 336" role="img" aria-label="Inspector at work on a steel deck, framed in an oval">
  <defs>
    <linearGradient id="aboutGrad" x1="0" y1="0" x2="1" y2="1">
      <stop offset="0" stop-color="#6e5a4a"/>
      <stop offset=".5" stop-color="#5a3f30"/>
      <stop offset="1" stop-color="#3f2e26"/>
    </linearGradient>
  </defs>
  <ellipse cx="202" cy="168" rx="200" ry="160" transform="rotate(-20 202 168)" fill="none" stroke="#7a5a48" stroke-width="2"/>
  <ellipse cx="202" cy="166" rx="186" ry="146" transform="rotate(-20 202 166)" fill="url(#aboutGrad)"/>
</svg>
<h2 class="abs heading about-title"><b>WHO</b> WE ARE</h2>
<p class="abs about-lead">Our operations are split into two divisions, Kelvota Inspection Services and Kelvota Engineering services.</p>
<p class="abs about-body">We pick the best talent from the industry and have heavily invested in our developing our staff skills further through regular rigorous external and internal training to keep up with the industry trends.</p>
<a class="pill pill-outline-navy about-btn">LEARN MORE</a>

<!-- lavender backdrop + services band -->
<svg class="abs" style="left:0;top:1190px" width="1200" height="1320" viewBox="0 0 1200 1320">
  <polygon points="0,500 1200,580 1200,1297 0,1203" fill="#e9ebf6"/>
  <polygon points="0,1203 1200,1297 0,1308" fill="#1b2358"/>
  <polygon points="780,78 1200,12 1200,450" fill="#1b2358"/>
  <polygon points="0,3 780,78 1200,60 1200,618 0,502" fill="#a8091a"/>
  <polygon points="0,3 400,40 0,502" fill="#b0101f" opacity=".5"/>
</svg>
<h2 class="abs heading services-title"><b>OUR</b> SERVICES</h2>
<p class="abs services-text">With roots in Mombasa, we have over 15 years' experience in NDT, Mechanical engineering and Marine services. We enjoy a regional presence in The larger Eastern and Central African Region.</p>

<svg class="abs" style="left:66px;top:1628px" width="24" height="36" viewBox="0 0 24 36"><path d="M18 4L5 18l13 14" fill="none" stroke="#fff" stroke-width="5"/></svg>
<svg class="abs" style="left:1106px;top:1628px" width="24" height="36" viewBox="0 0 24 36"><path d="M6 4l13 14L6 32" fill="none" stroke="#fff" stroke-width="5"/></svg>

<div class="service-card" style="left:124px;background:linear-gradient(160deg,#2b2a24,#1a1a1a 60%,#2c2c28)" role="img" aria-label="Inspectors in hard hats on site">
  <svg class="icon" width="70" height="70" viewBox="0 0 70 70"><circle cx="38" cy="30" r="20" fill="none" stroke="#fff" stroke-width="3"/><path d="M24 44L8 60" stroke="#fff" stroke-width="5"/><path d="M30 32l6 6 12-14" fill="none" stroke="#fff" stroke-width="3"/></svg>
  <h3>INSPECTION<span>SERVICES</span></h3>
  <a class="pill pill-outline-white">LEARN MORE</a>
</div>
<div class="service-card" style="left:454px;background:linear-gradient(170deg,#2b3aa6,#1f2d8c 55%,#16206a);box-shadow:0 10px 22px rgba(0,0,0,.35)" role="img" aria-label="Vessel at a harbour at dusk">
  <svg class="icon" width="70" height="70" viewBox="0 0 70 70"><rect x="4" y="26" width="12" height="22" fill="none" stroke="#fff" stroke-width="3"/><rect x="54" y="26" width="12" height="22" fill="none" stroke="#fff" stroke-width="3"/><circle cx="35" cy="37" r="14" fill="none" stroke="#fff" stroke-width="3"/><path d="M16 37h5M49 37h5M35 23V8M24 8h22" stroke="#fff" stroke-width="3"/></svg>
  <h3>NDT<span>SERVICES</span></h3>
  <a class="pill pill-outline-white">LEARN MORE</a>
</div>
<div class="service-card" style="left:784px;background:linear-gradient(160deg,#4a4a46,#2f302f 60%,#3a3935)" role="img" aria-label="Engineers on site with tanks behind">
  <svg class="icon" width="70" height="70" viewBox="0 0 70 70"><path d="M14 30a21 21 0 0 1 42 0z" fill="none" stroke="#fff" stroke-width="3"/><path d="M10 30h50M35 9v8" stroke="#fff" stroke-width="3"/><path d="M16 66V54a19 10 0 0 1 38 0v12" fill="none" stroke="#fff" stroke-width="3"/></svg>
  <h3>ENGINEERING<span>SERVICES</span></h3>
  <a class="pill pill-outline-white">LEARN MORE</a>
</div>

<!-- blogs -->
<h2 class="abs heading blogs-title"><b>RECENT</b> BLOGS</h2>
<article class="blog-card" style="left:127px">
  <div class="thumb" style="background:linear-gradient(180deg,#b7bcc0,#8a8a72 45%,#6e7a3c)" role="img" aria-label="Yellow pipework beside a concrete wall"></div>
  <div class="text">
    <div class="blog-date"><svg width="13" height="13" viewBox="0 0 13 13"><rect x="1" y="2" width="11" height="10" fill="none" stroke="#a8091a" stroke-width="1.5"/><path d="M1 5h11M4 0v3M9 0v3" stroke="#a8091a" stroke-width="1.5"/></svg>25 JAN 2020</div>
    <div class="blog-title">Augiat in pede Fusce tellus Sed metus augue</div>
    <p class="blog-excerpt">Nunc tempus felis vitae urna Vivamus porttitor neque at volutpat rutrum purus nisi eleifend libero a tempus libero lectus</p>
    <a class="blog-more">READ MORE</a>
  </div>
</article>
<article class="blog-card" style="left:620px">
  <div class="thumb" style="background:linear-gradient(180deg,#6c6f78,#3d4a86 50%,#5a5550)" role="img" aria-label="Technician working on a pipe flange"></div>
  <div class="text">
    <div class="blog-date"><svg width="13" height="13" viewBox="0 0 13 13"><rect x="1" y="2" width="11" height="10" fill="none" stroke="#a8091a" stroke-width="1.5"/><path d="M1 5h11M4 0v3M9 0v3" stroke="#a8091a" stroke-width="1.5"/></svg>25 JAN 2020</div>
    <div class="blog-title">Praesent sit amet est In dictum dolor dictum</div>
    <p class="blog-excerpt">Nunc tempus felis vitae urna Vivamus porttitor neque at volutpat rutrum purus nisi eleifend libero a tempus libero lectus</p>
    <a class="blog-more">READ MORE</a>
  </div>
</article>

<!-- sectors -->
<h2 class="abs heading sectors-title"><b>WE MAINLY</b><br>WORK IN</h2>
<p class="abs sectors-text">Nunc tempus felis vitae urna Vivamus porttitor neque</p>
<a class="pill pill-outline-navy sectors-btn">LEARN MORE</a>
<div class="sector-tile" style="left:405px;background:linear-gradient(160deg,#8a6a55,#b8aea0 50%,#6b6a66)" role="img" aria-label="Pipe section under inspection"><span>Storage Terminals</span></div>
<div class="sector-tile" style="left:636px;background:linear-gradient(170deg,#b9bab5,#8e8a60 50%,#6f6a3e)" role="img" aria-label="Yellow refinery pipework"><span>Refineries</span></div>
<div class="sector-tile" style="left:868px;background:linear-gradient(160deg,#7e8288,#4f5459 50%,#5f605e)" role="img" aria-label="Pipes stacked at an offshore yard"><span>Oil and Gas offshore</span></div>

<!-- contact -->
<div class="abs contact-band" role="img" aria-label="Pipeline work site tinted red"></div>
<h2 class="abs heading contact-title"><b>CONTACT</b> US</h2>
<p class="abs contact-text">Nunc tempus felis vitae urna Vivamus porttitor neque at volutpat rutrum purus nisi eleifend libero a tempus libero lectus feugiat felis Morbi diam mauris viverra in gravida eu mattis in ante Morbi eget arcu Morbi porta libero id ullamcorper nonummy</p>
<a class="pill contact-btn">GET IN TOUCH</a>

<!-- footer -->
<footer class="abs site-footer">
  <div class="footer-brand">
    <div class="brand-dot"></div>
    <div class="brand-name">KELVOTA<br>ENGINEERING</div>
  </div>
  <div class="footer-col" style="left:424px">
    <h4>COMPANY</h4>
    <ul><li>About Us</li><li>Our Services</li><li>Inspection</li><li>Blogs</li><li>Contact Us</li></ul>
  </div>
  <div class="footer-col" style="left:620px">
    <h4>CONTACT US</h4>
    <ul><li>P. O. Box 40518 - 80100</li><li>Mombasa, Kenya</li><li>T: +254 0203114820 / 1</li><li>C: +254711305286</li><li>info@kelvota-eng.com</li></ul>
  </div>
  <div class="footer-col" style="left:869px">
    <h4>FOLLOW US</h4>
    <div class="social"><span aria-label="Social page one"></span><span aria-label="Social page two"></span><span aria-label="Social page three"></span><span aria-label="Social page four"></span></div>
  </div>
</footer>
<div class="abs copyright">© 2020 Company Name | All Rights Reserved</div>

</body>
</html>
```